Box Package Design for a brand new patented shower head

We need a box packaging design and a design for a manual(insert) that goes inside the box. This is for a brand new patented shower head soon to be launched. We have been in the tapware business for over 25 years, always providing best quality innovative products, the "only-one-of-its-kind" in the market.
We already have all the contents, images, and specific design instructions ready. We have uploaded the 2 files regarding the design instructions (one for the box, and one for the manual).
Because of the file size, related files you need to work on can be downloaded through the following Cargoshelf links
Box design:
https://www.cargoshelf-files.net/s/tkvrpwm2zq8hdn/Box_design.zip?dl=0
Manual design:
https://www.cargoshelf-files.net/s/wvn4rkpa7tmq2x/Manual_design.zip?dl=0
Updates
Reason: We would like to have more time to receive designs and communicate with the designers.
Thank you for your interest in this project.
We have extended deadline to receive more designs and to communicate.
Also we have guaranteed the payment :) Looking forward to your great designs!
Reason: Needed more time for changes and communication with designers.
Target Market(s)
Customers interested in bathroom/shower/tap upgrades, DIY home renovations
Requirements
Must have
- Please include all the design instructions we have specified in the PPT files.
Nice to have
- It would be great to see some creative layouts using our current images.

```html
<!DOCTYPE html>
<html lang="en">
<head>
<meta charset="utf-8">
<title>Shower Head Manual</title>
<link href="https://fonts.googleapis.com/css2?family=Courgette&family=Roboto+Condensed:wght@400;500&family=Arimo:wght@400&display=swap" rel="stylesheet">
<style>
:root{
  --sky-top:#2e8fd8;
  --sky-mid:#5fb4ec;
  --sky-low:#cfeefa;
  --panel-blue:#0b7bcc;
  --navy:#17324d;
  --band:#1d3c5e;
  --aqua-title:#45e3d8;
  --teal:#34cfdc;
  --ink:#1b2c38;
  --white:#ffffff;
  --photo-warm:#c9a676;
  --photo-wall:#e9e6e2;
}
*{margin:0;padding:0;box-sizing:border-box}
html,body{width:1200px;height:848px;overflow:hidden}
body{position:relative;background:linear-gradient(180deg,var(--sky-top) 0%,var(--sky-mid) 55%,var(--sky-low) 100%);font-family:"Roboto Condensed",Arial,sans-serif;color:var(--ink)}
.abs{position:absolute}
.section-title{position:absolute;height:42px;display:flex;align-items:center;justify-content:center;
  background:linear-gradient(90deg,rgba(29,60,94,0) 0%,var(--band) 22%,var(--band) 78%,rgba(29,60,94,0) 100%);
  font-family:"Courgette",cursive;font-size:27px;color:var(--aqua-title);text-shadow:0 1px 2px rgba(0,0,0,.5)}
.parts-board{left:40px;top:62px;width:315px;height:370px;background:var(--white);border-radius:8px}
.parts-drawing{left:95px;top:6px;width:155px;height:355px;border-radius:6px;background:linear-gradient(180deg,#e6e9ec,#c9cfd4)}
.part-label{position:absolute;font-family:Arimo,Arial,sans-serif;font-size:7.4px;color:#333;line-height:1.2}
.install-panel{left:15px;top:486px;width:363px;height:356px;background:var(--teal)}
.install-icons{left:6px;top:6px;width:110px;height:344px;background:var(--white)}
.install-step{position:absolute;left:118px;width:245px;height:66px;display:flex;align-items:center;justify-content:center;text-align:center;font-size:11.6px;line-height:1.15;color:var(--ink)}
.install-icon{position:absolute;left:14px;width:82px;height:54px;border-radius:4px;background:linear-gradient(135deg,#eef0f2,#c9ced3)}
.pointer{position:absolute;left:116px;width:0;height:0;border-top:9px solid transparent;border-bottom:9px solid transparent;border-right:10px solid var(--white)}
.hero-photo{left:510px;top:90px;width:190px;height:108px;border-radius:6px;background:linear-gradient(160deg,var(--photo-wall),var(--photo-warm))}
.step-card{position:absolute;left:409px;width:364px;border-radius:8px;overflow:hidden;background:var(--navy)}
.step-photos{display:flex;gap:2px}
.step-photo{flex:1;background:linear-gradient(170deg,var(--photo-wall) 0%,var(--photo-wall) 40%,var(--photo-warm) 100%)}
.step-photo.dark{background:linear-gradient(170deg,#d8d4cf,#b89868)}
.step-caption{color:var(--white);font-size:11.6px;line-height:1.12;padding:8px 10px 6px 9px}
.info-panel{left:800px;top:0;width:400px;height:848px;background:var(--panel-blue)}
.info-text{position:absolute;left:818px;width:370px;color:var(--white);font-family:Arimo,Arial,sans-serif;font-size:9.1px;line-height:15.4px}
.info-text p{margin-bottom:15.4px}
.info-text .tight{margin-bottom:0}
.info-text .dash{padding-left:10px}
.spec-list{position:absolute;left:818px;top:740px;color:var(--white);font-family:Arimo,Arial,sans-serif;font-size:13px;line-height:20.2px}
</style>
</head>
<body>

<!-- Right information panel -->
<svg class="abs" style="left:780px;top:0" width="420" height="848" aria-hidden="true">
  <path d="M420 0 H20 Q40 0 20 0 L20 848 H420 Z" fill="#0b7bcc"/>
  <path d="M20 0 C60 0 120 -5 160 0 L20 0 Z" fill="#0b7bcc"/>
</svg>

<!-- Name of Part -->
<div class="section-title" style="left:60px;top:15px;width:250px">Name of Part</div>
<div class="abs parts-board">
  <div class="abs parts-drawing" role="img" aria-label="Exploded technical drawing of the shower head parts, bracket and hose"></div>
  <span class="part-label" style="left:45px;top:34px">G. White O-ring</span>
  <span class="part-label" style="left:30px;top:47px">H. Watering plate</span>
  <span class="part-label" style="left:18px;top:78px">I. Shower head cap</span>
  <span class="part-label" style="left:248px;top:33px">A. Shower head</span>
  <span class="part-label" style="left:257px;top:78px">B. Top O-ring</span>
  <span class="part-label" style="left:254px;top:104px">C. Water filter</span>
  <span class="part-label" style="left:244px;top:156px">D. Ceramic filter</span>
  <span class="part-label" style="left:142px;top:158px">J. Drill-free<br>bracket</span>
  <span class="part-label" style="left:134px;top:220px">K. Flexible hose</span>
  <span class="part-label" style="left:10px;top:253px">L. Water saver<br>&nbsp;&nbsp;(Pre-fitted<br>&nbsp;&nbsp;inside hose)</span>
  <span class="part-label" style="left:256px;top:270px">E. Handle</span>
  <span class="part-label" style="left:248px;top:348px">F. Bottom O-ring</span>
</div>

<!-- Installation -->
<div class="section-title" style="left:55px;top:444px;width:290px">Installation</div>
<div class="abs install-panel">
  <div class="abs install-icons">
    <div class="install-icon" style="top:6px" role="img" aria-label="Removing old shower head anti-clockwise"></div>
    <div class="install-icon" style="top:75px" role="img" aria-label="Fitting bracket clockwise to outlet"></div>
    <div class="install-icon" style="top:143px" role="img" aria-label="Bracket vertical with thread facing down"></div>
    <div class="install-icon" style="top:213px" role="img" aria-label="Connecting hose to shower head and bracket"></div>
    <div class="install-icon" style="top:282px" role="img" aria-label="Shower head placed on bracket"></div>
  </div>
  <div class="pointer" style="top:27px"></div>
  <div class="pointer" style="top:98px"></div>
  <div class="pointer" style="top:166px"></div>
  <div class="pointer" style="top:236px"></div>
  <div class="pointer" style="top:304px"></div>
  <div class="install-step" style="top:2px">Remove the existing shower head by turning it anti-clockwise</div>
  <div class="install-step" style="top:70px">Fit the drill-free bracket clockwise to the shower head outlet. Tighten by hand only</div>
  <div class="install-step" style="top:138px">Ensure that the bracket is vertical and that the thread faces straight down</div>
  <div class="install-step" style="top:208px">Connect the hose to the shower head and to the bracket. The nut side of the hose should connect to the bracket. Make sure washers are placed inside the hose. Tighten by hand only</div>
  <div class="install-step" style="top:282px">To adjust the position of the bracket holder, place the shower head onto the bracket and use it as a lever to swivel the holder up and down.</div>
</div>

<!-- Assembly -->
<div class="section-title" style="left:405px;top:24px;width:385px;font-size:25px">Shower Head Assembly Instructions</div>
<div class="abs hero-photo" role="img" aria-label="Photo of all shower head components laid out on a table"></div>

<div class="step-card" style="top:213px">
  <div class="step-photos" style="height:85px">
    <div class="step-photo" role="img" aria-label="Ceramic filter beside handle"></div>
    <div class="step-photo" role="img" aria-label="Ceramic filter inserted in handle"></div>
  </div>
  <div class="step-caption">1. Insert (D) Ceramic filter into (E) Handle. Make sure the propeller side<br>&nbsp;&nbsp;&nbsp;of the Ceramic filter goes into the Handle first, facing downwards.</div>
</div>

<div class="step-card" style="top:353px">
  <div class="step-photos" style="height:83px">
    <div class="step-photo" style="flex:0 0 170px" role="img" aria-label="Water filter on top of handle"></div>
    <div class="step-photo" style="flex:0 0 152px" role="img" aria-label="Water filter inserted in handle"></div>
    <div class="step-photo dark" role="img" aria-label="Close-up of water filter orientation"></div>
  </div>
  <div class="step-caption">2. Insert (C) Water filter into (E) Handle. Make sure the fat end of the<br>&nbsp;&nbsp;&nbsp;Water filter goes into the Handle first, facing downwards.</div>
</div>

<div class="step-card" style="top:492px">
  <div class="step-photos" style="height:84px">
    <div class="step-photo" role="img" aria-label="Watering plate placed in shower head cap"></div>
    <div class="step-photo" role="img" aria-label="White O-ring placed on watering plate"></div>
  </div>
  <div class="step-caption">3. Place (H) Watering plate in the (I) Shower head cap. Make sure the<br>&nbsp;&nbsp;&nbsp;side of the Watering plate with the engravings faces outwards<br>&nbsp;&nbsp;&nbsp;(facing down on the table as in picture). Place the (G) White O-ring<br>&nbsp;&nbsp;&nbsp;inside onto the Watering plate. Make sure the fat side of the White<br>&nbsp;&nbsp;&nbsp;O-ring faces the Watering plate.</div>
</div>

<div class="step-card" style="top:673px">
  <div class="step-photos" style="height:94px">
    <div class="step-photo" role="img" aria-label="Shower head screwed onto handle"></div>
    <div class="step-photo" role="img" aria-label="Shower head cap screwed on"></div>
  </div>
  <div class="step-caption">4. Screw (A) Shower head onto the (E) Handle. Screw (I) Shower head<br>&nbsp;&nbsp;&nbsp;cap onto the Shower head. Make sure the (B) Top O-ring and<br>&nbsp;&nbsp;&nbsp;(F) Bottom O-ring are in the place properly. Missing or damaged<br>&nbsp;&nbsp;&nbsp;O-rings may cause leaks.</div>
</div>

<!-- Maintenance -->
<div class="section-title" style="left:860px;top:16px;width:275px">Maintenance</div>
<div class="info-text" style="top:64px">
  <p>It is recommended that you regularly clean your shower head to prevent blockage and/or damages. Regular maintenance will also ensure optimal water pressure level. The frequency of your maintenance routine should vary depending on the quality of water in your location.</p>
  <p>Because the photo-etched holes are very fine, lack of maintenance can cause build-up of lime, calcium and other particles in the holes. This can cause water pressure to exceed product specifications, leading to failures such as cracked parts, leaks, buckled shower plate, etc.</p>
  <p>To correctly maintain your product, simply disassemble the shower head and follow the instructions below.</p>
  <p class="tight">1. The ceramic filter is semi-permanent and will not need replacement if maintained correctly and if it is not damaged physically.&nbsp; Wash the ceramic filter under warm water and give it a good shake while rinsing to remove any build-up of dirt and other contaminants.</p>
  <p class="tight">2. To clean the watering plate:</p>
  <p class="tight dash">- Soak the watering plate in a bowl filled with white vinegar or fresh Fizzola</p>
  <p class="tight dash">-&nbsp; Cover the bowl with plastic wrap</p>
  <p class="tight dash">-&nbsp; Leave if for several hours, or overnight or longer if build-up is severe</p>
  <p class="tight dash">- Minerals, lime, calcium and other build-ups will dissolve away from the holes</p>
  <p class="tight dash">- Rinse the watering plate with cold water</p>
  <p class="tight">3. Wash other parts of the shower head and assemble back together, making sure all the components are placed correctly. (See “Assembly Instructions” for detailed information)</p>
  <p class="tight">4. The water filter can be replaced when dirty, or when the water pressure drops remarkably. Replacement cycles should vary depending on the amount of water consumed, water pressure, quality of the water in your location, etc. Average replacement cycle is once every 3 months.</p>
</div>

<!-- Important -->
<div class="section-title" style="left:870px;top:498px;width:255px">Important</div>
<div class="info-text" style="top:545px">
  <p class="tight">Please read the manual before use, and follow the maintenance guidelines regularly to avoid possible damages or failures</p>
  <p class="tight">Do not soak the shower head in water for a long time.</p>
  <p class="tight">Do not use this product with hot water over 70°C.</p>
  <p class="tight">Some metal pieces may have sharp edges. Please exercise care when assembling.</p>
  <p class="tight">Gravity Fed users or users with under 100kpa water pressure in the region may not see improvements in their water pressure and/or may see fluctuations in the water temperature. Users with instantaneous hot water system may also see fluctuations in their water temperature.</p>
</div>

<!-- Specification -->
<div class="section-title" style="left:870px;top:692px;width:260px">Specification</div>
<div class="spec-list">
  <div>Materials: Heat-resistant PC</div>
  <div>Recommended temperature: 0 ~ 70</div>
  <div>Watering plate holes: Ø 0.20 / 412EA</div>
  <div>Made in Korea</div>
</div>

</body>
</html>
```